Corporate Design für logopädische Praxis
Zielgruppe
Ich gründe eine logopädische Praxis, die Sprachtherapie sowohl für Erwachsene als auch Kinder anbietet und damit ein Logo benötigt, das jede Altersgruppe anspricht und 'Lindenhof' als fachliche und menschliche Qualitätszeit interpretiert.
Aufgabenstellung
Ich bevorzuge ein klares Design, welches das Wortspiel der 'Lindenhof' im Idealfall aufgreift und den Patienten vermittelt, dass sowohl die fachliche Qualität der Behandlung als auch die Ebene von Empathie und Patientenorientierung im zwischenmenschlichen Umgang für die Praxis zentral sind.

```html
<!DOCTYPE html>
<html lang="de">
<head>
<meta charset="utf-8">
<title>Lindenhof – Visitenkarte</title>
<link href="https://fonts.googleapis.com/css2?family=Poppins:wght@300;400;600&display=swap" rel="stylesheet">
<style>
  :root {
    --page-bg: #fcfcfc;
    --brand-lilac: #a290aa;
    --band-lilac: #ded7e0;
    --card-light: #f6f5fa;
    --name-lilac: #a08aa8;
    --text-grey: #6e6a73;
    --decor-lilac: #ecebf1;
    --white: #ffffff;
  }
  * { margin: 0; padding: 0; box-sizing: border-box; }
  html, body {
    width: 1107px;
    height: 1200px;
    overflow: hidden;
    background: var(--page-bg);
    font-family: "Poppins", sans-serif;
  }
  .canvas { position: relative; width: 1107px; height: 1200px; }

  .card {
    position: absolute;
    width: 589px;
    height: 380px;
    overflow: hidden;
  }

  /* Front */
  .card-front { left: 249px; top: 198px; background: var(--brand-lilac); }
  .brand-mark {
    position: absolute;
    left: 0; right: 0;
    top: 118px;
    display: flex;
    justify-content: center;
    align-items: center;
    gap: 14px;
    color: var(--white);
  }
  .brand-dot {
    width: 34px; height: 34px;
    border-radius: 50%;
    background: var(--white);
  }
  .brand-name {
    font-weight: 400;
    font-size: 56px;
    line-height: 1;
    letter-spacing: 1px;
  }
  .tagline {
    position: absolute;
    left: 0; right: 0;
    top: 221px;
    text-align: center;
    color: var(--white);
    font-weight: 300;
    font-size: 25px;
    letter-spacing: 1.5px;
    line-height: 1;
  }

  /* Back */
  .card-back { left: 251px; top: 610px; background: var(--card-light); }
  .top-band {
    position: absolute; left: 0; top: 0;
    width: 100%; height: 24px;
    background: var(--band-lilac);
  }
  .decor-circle {
    position: absolute;
    left: 518px; top: 50px;
    width: 140px; height: 140px;
    border-radius: 50%;
    background: var(--decor-lilac);
  }
  .person { position: absolute; left: 40px; top: 74px; }
  .person-name {
    color: var(--name-lilac);
    font-weight: 600;
    font-size: 21px;
    letter-spacing: 2px;
    line-height: 1.1;
  }
  .person-title {
    color: var(--text-grey);
    font-weight: 400;
    font-size: 13px;
    letter-spacing: 2px;
    line-height: 1.3;
  }
  .contact {
    position: absolute;
    left: 40px;
    color: var(--text-grey);
    font-weight: 300;
    font-size: 16px;
    letter-spacing: 3px;
    line-height: 20px;
  }
  .contact-phone { top: 214px; }
  .contact-phone .label { display: inline-block; width: 55px; }
  .contact-web { top: 281px; }
</style>
</head>
<body>
  <main class="canvas">
    <section class="card card-front" aria-label="Vorderseite">
      <div class="brand-mark">
        <span class="brand-dot" aria-hidden="true"></span>
        <span class="brand-name">Lindenhof</span>
      </div>
      <p class="tagline">PRAXIS FÜR LOGOPÄDIE</p>
    </section>

    <section class="card card-back" aria-label="Rückseite">
      <div class="top-band"></div>
      <div class="decor-circle" aria-hidden="true"></div>
      <div class="person">
        <p class="person-name">Jule Berkhan</p>
        <p class="person-title">Diplom-Rehabilitationspädagogin</p>
      </div>
      <div class="contact contact-phone">
        <p><span class="label">TEL:</span>0561 72 83 90 17</p>
        <p><span class="label">FAX:</span>0561 72 83 90 18</p>
      </div>
      <div class="contact contact-web">
        <p>www.lindenhof.de</p>
        <p>j.berkhan@lindenhof.de</p>
      </div>
    </section>
  </main>
</body>
</html>
```